Guided Study Tour - Klangtage Wendorf Two Sided Flyer

We need a two-sided flyer for a Guided Study Tour to Klangtage Wendorf. We want beautiful pictures of Germany and if possible some of the Halbig venues our participants will be visiting. I have also provided the content that needs to be included. Also, in the attached document I provided a link to the Klangtage event. Please read and watch the video to be inspired.
This flyer should be beautiful and engaging. It needs to grab your attention right away and really highlight the wonderful things that they will be doing and that are included in the tour. This is a once in a lifetime opportunity for people to experience. We are targeting Music Directors and Music professionals.
Both attached logos need to be present on the flyer.

```html
<!DOCTYPE html>
<html lang="en">
<head>
<meta charset="utf-8">
<title>Guided Study Tour – Klangtage Wendorf Flyer</title>
<link href="https://fonts.googleapis.com/css2?family=Montserrat:wght@300;400;600;700&family=Great+Vibes&family=EB+Garamond:ital@1&display=swap" rel="stylesheet">
<style>
:root{
  --bg:#6f6f6f;
  --paper:#f1f1f3;
  --red:#c41f2c;
  --orange:#fbab4b;
  --purple:#6c3b8f;
  --navy:#1f2a4e;
  --ink:#2d2d33;
  --dark:#141416;
  --white:#ffffff;
}
*{margin:0;padding:0;box-sizing:border-box}
html,body{width:1200px;height:1018px;overflow:hidden;background:var(--bg)}
body{position:relative;font-family:'Montserrat',sans-serif;color:var(--ink)}
.page{position:absolute;top:170px;width:508px;height:717px;background:var(--paper);overflow:hidden}
.page--front{left:70px}
.page--back{left:628px}
.abs{position:absolute}

/* front */
.top-band{left:0;top:0;width:508px;height:48px;background:linear-gradient(90deg,#7a2a45,#4a2c5e 50%,#6b3154)}
.top-rule{left:0;top:48px;width:508px;height:4px;background:var(--orange)}
.hero{left:0;top:52px;width:508px;height:311px;background:linear-gradient(90deg,#f3f2f4 0%,#e4dfe2 38%,#b9aaa8 62%,#a59490 100%)}
.statue{left:292px;top:58px;width:210px;height:305px;background:linear-gradient(180deg,#3b3230,#1e1a19 70%,#2a2422)}
.title-script{left:24px;top:113px;font-family:'Great Vibes',cursive;font-size:22px;color:var(--purple)}
.title-main{left:42px;top:130px;font-family:'Great Vibes',cursive;font-size:74px;line-height:1;background:linear-gradient(90deg,var(--purple),var(--red));-webkit-background-clip:text;background-clip:text;color:transparent}
.date-box{left:26px;top:244px;padding:3px 8px;background:#f6d9b0;font-size:8.6px;color:var(--navy)}
.date-note{left:28px;top:270px;font-size:7.4px;line-height:1.3;color:var(--navy)}
.divider-navy{left:0;top:363px;width:255px;height:8px;background:var(--navy)}
.divider-orange{left:255px;top:363px;width:253px;height:8px;background:var(--orange)}
.col-rule{left:253px;top:394px;width:2px;height:188px;background:var(--red)}
.col-head{font-size:17.5px;font-weight:700;color:var(--red);white-space:nowrap}
.ticks{list-style:none;font-size:10px;line-height:15.4px;font-weight:400}
.ticks li{position:relative;padding-left:14px;white-space:nowrap}
.ticks li::before{content:"✔";position:absolute;left:0;top:0;font-size:9px;color:#444}
.ticks .cont{padding-left:22px}
.ticks .cont::before{content:none}
.featured-head{left:29px;top:536px;font-size:10.4px;font-weight:700;color:var(--red)}
.featured{left:29px;top:550px;font-size:9.6px;line-height:12px}
.quote{left:0;top:664px;width:508px;text-align:center;font-family:'EB Garamond',serif;font-style:italic;font-size:8.6px;line-height:12px;color:var(--red)}
.quote small{display:block;font-size:6.4px;line-height:9px}

/* back */
.city-photo{left:0;top:0;width:508px;height:320px;background:linear-gradient(180deg,#d37e64 0%,#6b5a8a 22%,#2e3560 48%,#3a2d3a 70%,#8a5a2c 100%)}
.intro-box{left:270px;top:66px;width:238px;height:104px;padding:6px 8px;background:rgba(28,28,70,.75);color:var(--white);font-size:8.7px;line-height:12px}
.incl-head{left:22px;top:318px;font-size:15px;font-weight:700;color:var(--red)}
.incl{font-size:8.8px;line-height:13.6px}
.incl .cont{padding-left:28px}
.person{left:50px;top:560px;width:220px;height:157px;background:radial-gradient(ellipse at 45% 40%,#5a5a5c,#1a1a1c 70%)}
.bio{left:202px;top:570px;width:290px;font-size:7.1px;line-height:12px;color:var(--white)}
.bio b{font-weight:600;color:var(--orange);font-variant:small-caps;font-size:8.6px}
.email{left:214px;top:684px;font-size:8.6px;color:var(--orange)}
.logo{top:688px;display:flex;align-items:center;gap:5px;font-size:10.5px;font-weight:600;color:var(--white)}
.logo i{display:block;width:14px;height:14px;border-radius:50%;background:var(--white)}
.logo--left{left:33px}
.logo--right{left:370px}
</style>
</head>
<body>

<section class="page page--front">
  <div class="abs top-band" role="img" aria-label="Photo of stained glass church windows"></div>
  <div class="abs top-rule"></div>
  <div class="abs hero" role="img" aria-label="Photo of a church facade in soft light"></div>
  <div class="abs statue" role="img" aria-label="Photo of a bronze composer statue in front of the church"></div>
  <div class="abs title-script">Guided Study Tour</div>
  <div class="abs title-main">Klangtage</div>
  <div class="abs date-box">June 12-16, 2019 | Wendorf, Germany</div>
  <p class="abs date-note">Plus day trips to Wittenberg and Weimar,<br>and guided tours in Berlin, Dresden,<br>and two nights in Prague!</p>
  <div class="abs divider-navy"></div>
  <div class="abs divider-orange"></div>

  <div class="abs" style="left:29px;top:386px">
    <h2 class="col-head">Klangtage Highlights:</h2>
  </div>
  <ul class="abs ticks" style="left:15px;top:412px;width:235px">
    <li>More than 100 Concerts in 42 different</li>
    <li class="cont">Halbig venues</li>
    <li>World Class Musicians &amp; Celebrated</li>
    <li class="cont">Recording Artists</li>
    <li>Day trips to Weimer &amp; Dresden</li>
    <li>Bilingual pre-concert talks &amp; lectures with</li>
    <li class="cont">Halbig Scholars</li>
  </ul>
  <div class="abs featured-head">Featured Performers:</div>
  <p class="abs featured">Joan Serrat, Tomas Kerkhof, Cantorum,<br>Wendorf Hall Orchestra, Lumina,<br>&amp; the Wendorf Boys' Choir</p>

  <div class="abs col-rule"></div>
  <div class="abs" style="left:285px;top:386px">
    <h2 class="col-head">Study Tour Highlights:</h2>
  </div>
  <ul class="abs ticks" style="left:271px;top:412px;width:235px;font-size:9.6px">
    <li>Access to dress rehearsals</li>
    <li>Meet the artist opportunities</li>
    <li>Post-concert discussions led by Dan Marlow</li>
    <li>Study sessions on Halbig's B-Minor Mass,</li>
    <li class="cont">Magnificat, St. John Passion,</li>
    <li class="cont">St. Matthew Passion &amp; Weimar</li>
    <li class="cont">Cantatashours</li>
    <li>Guidance in planning individual</li>
    <li class="cont">concert itinerary</li>
    <li>Professional development or continuing</li>
    <li class="cont">education credit</li>
  </ul>

  <svg class="abs" style="left:0;top:585px" width="508" height="132" viewBox="0 0 508 132">
    <path d="M80,62 Q260,-26 508,52 L508,60 Q260,-16 80,62Z" fill="var(--purple)"/>
    <path d="M0,95 Q260,-30 508,60 L508,78 Q260,-10 0,110Z" fill="var(--red)"/>
    <path d="M0,110 Q260,-10 508,78 L508,96 Q260,12 0,125Z" fill="var(--orange)"/>
    <path d="M0,132 L0,128 Q260,105 508,110 L508,132Z" fill="var(--orange)"/>
  </svg>
  <p class="abs quote">"This is where it all has begun...this is why our guests have tears in their eyes<br>listening to the St. Matthew Passion or the B-Minor Mass"<small>~ Martin Auler, Musicologist, Festival Director</small></p>
</section>

<section class="page page--back">
  <div class="abs city-photo" role="img" aria-label="Night photo of a cathedral city skyline with a lit railway bridge"></div>
  <svg class="abs" style="left:0;top:200px" width="508" height="130" viewBox="0 0 508 130">
    <path d="M0,60 Q180,150 508,70 L508,130 L0,130Z" fill="var(--paper)"/>
    <path d="M0,52 Q180,140 508,60 L508,82 Q200,150 0,66Z" fill="var(--orange)"/>
    <path d="M120,96 Q300,110 508,58 L508,70 Q330,130 120,96Z" fill="var(--red)"/>
  </svg>
  <p class="abs intro-box">After many years of attending Klangtage, Dr. Daniel Marlow has partnered with Meridian Classic to create a memorable study tour centered around the 2019 festival. Meridian Classic Tours, powered by Lindqvist Tours, is utilizing their more than 100 years of combined travel expertise to design a custom tour for all who love the music of the Baroque era.</p>

  <svg class="abs" style="left:20px;top:280px" width="56" height="36" viewBox="0 0 56 36" aria-hidden="true">
    <path d="M2,30 L20,22 L14,34 L20,34 L32,18 L50,10 Q56,6 50,4 L34,10 L24,2 L18,2 L24,14 L10,20 L4,16 L0,16 L4,24Z" fill="var(--purple)"/>
  </svg>
  <h2 class="abs incl-head">TRIP INCLUSIONS</h2>
  <ul class="abs ticks incl" style="left:22px;top:340px;width:240px">
    <li>Roundtrip Airfare from Austin</li>
    <li>13 Nights Accomodations,</li>
    <li class="cont">3 Star Hotels with A/C</li>
    <li>Daily Breakfast</li>
    <li>Access to rehearsal sessions</li>
    <li>Pirvate Luxury Coach Transfer Services</li>
    <li class="cont">for airport transfers and day tours to Berlin,</li>
    <li class="cont">Weimar and Dresden &amp; Prague.</li>
    <li>Professional Local Guides for City Tours in:</li>
    <li class="cont">Berlin, Weimar, Dresden &amp; Prague</li>
  </ul>
  <ul class="abs ticks incl" style="left:265px;top:340px;width:240px">
    <li>Entrance fees to: Composer's House,</li>
    <li class="cont">Painter's House, National Museum &amp;</li>
    <li class="cont">House of the Poet in Weimer, Old Town</li>
    <li class="cont">Church, Gallery of Old Masters, Castle of</li>
    <li class="cont">Prague, Castle Basilica, Old Palace,</li>
    <li class="cont">Goldsmiths' Lane, and the Castle Cathedral.</li>
    <li>All Applicable Taxes and Gratuities</li>
    <li class="cont">for Included Services, Guides, and Drivers</li>
    <li>$2 Million in Professional Liability Insurance</li>
    <li>24-hour Travel Support Staff</li>
  </ul>

  <svg class="abs" style="left:0;top:480px" width="508" height="237" viewBox="0 0 508 237">
    <path d="M0,70 Q240,-20 508,52 L508,237 L0,237Z" fill="var(--dark)"/>
    <path d="M0,46 Q240,-30 508,30 L508,52 Q240,-14 0,70Z" fill="var(--red)"/>
    <path d="M200,20 Q380,-4 508,30 L508,34 Q380,4 200,20Z" fill="var(--purple)"/>
    <path d="M0,70 Q240,-14 508,52 L508,66 Q240,6 0,86Z" fill="var(--orange)"/>
  </svg>
  <div class="abs person" role="img" aria-label="Photo of the tour leader conducting, seen from the side"></div>
  <p class="abs bio"><b>Daniel Marlow</b> is Director of Choral Studies at the Southern Plains University and the conductor of the Riverside Symphony Chorale and the Riverside Choral Artists, a professional chamber choir. A native Texan, his degrees are from Pinecrest College, Hollins State University and Western Coast University. Recent engagements include conducting the Hallström Requiem in Albany, NY, serving on the jury for the Aegean Choral Festival in Kavala, Greece and the International Choir Cup in Split, Croatia.</p>
  <div class="abs email">d.marlow@spu-music.edu</div>
  <div class="abs logo logo--left"><i></i>Lindqvist Tours</div>
  <div class="abs logo logo--right"><i></i>Meridian Classic</div>
</section>

</body>
</html>
```